Flat bootstrap design for existing site

I'm looking for a modern flat design based around an existing logo. This has to be a custom design (no external templates), and implemented into a bootstrap framework.

The logo is attached as 2 versions - choose whichever you want, that flows better with whatever design you choose.

Added screenshots of the existing site (currently using the default bootstrap layouts). Please make your designs around those pages in the screenshots (i.e. the homepage only has the postal code input and the header). The active page has 3 screenshots, because I wanted to illustrate the other states that would be visible (in the table rows).

This is a moving/junk removal website, just for some context.

Here's some example websites (flat designs) that I like, just to give you an idea of what I'm after.

https://www.plimvora.com/
https://dacklow.com/
https://trevanu.com/
https://quobrintal.com/en/

Coding

Coded - Design and coding required

Number of Pages Required

5+ page

Colors

Designer to choose colors to be used in the design.

Requirements
Must have
• It must be a modern/simple flat design, that is built around the existing logo (attached).
• It has to be implemented using bootstrap.

```html
<!DOCTYPE html>
<html lang="en">
<head>
<meta charset="utf-8">
<title>HAULVO – Booking Details</title>
<link href="https://fonts.googleapis.com/css2?family=Montserrat:wght@400;500;600;700&display=swap" rel="stylesheet">
<style>
:root{
  --brand:#4cc7f2;
  --brand-dark:#3aa9e0;
  --page:#f6f6f8;
  --panel:#f0f0f2;
  --panel-line:#dcdcdf;
  --field:#ffffff;
  --field-line:#d9d9dc;
  --ink:#1d1d1f;
  --ink-soft:#3a3a3c;
  --info-bg:#dde9f3;
  --info-ink:#4b6f8c;
  --accepted:#5aa531;
  --pending:#3d3d3d;
  --footer:#e3e3e5;
}
*{box-sizing:border-box;margin:0;padding:0}
html,body{width:1200px;height:939px;overflow:hidden}
body{font-family:"Montserrat",sans-serif;background:var(--page);color:var(--ink);position:relative}
.top-rule{position:absolute;left:0;top:0;width:1200px;height:3px;background:var(--brand)}
.brand{position:absolute;left:99px;top:34px;display:flex;align-items:center;gap:10px;font-size:40px;font-weight:700;color:var(--brand);letter-spacing:1px}
.brand-dot{width:22px;height:22px;border-radius:50%;background:var(--brand)}
.nav{position:absolute;top:33px;left:584px;display:flex;align-items:center;height:37px;font-size:13.5px;font-weight:500}
.nav a{text-decoration:none;color:var(--ink)}
.nav .active{color:var(--brand)}
.nav .how{margin-left:31px}
.nav .driver{margin-left:16px;background:var(--brand);color:#fff;height:37px;width:151px;display:flex;align-items:center;justify-content:center}
.nav .account{margin-left:16px}
.panel{position:absolute;left:99px;width:1003px;background:var(--panel);border:1px solid var(--panel-line)}
.booking{top:108px;height:324px}
.drivers{top:443px;height:324px}
.panel h2{position:absolute;left:56px;top:25px;font-size:17px;font-weight:500;letter-spacing:.3px}
.label{position:absolute;font-size:13px;color:var(--ink-soft)}
.field{position:absolute;background:var(--field);border:1px solid var(--field-line);font-size:13px;display:flex;align-items:center;padding-left:16px;color:var(--ink-soft)}
.field svg{position:absolute;right:12px}
.textarea{align-items:flex-start;padding-top:5px}
.btn-update{position:absolute;left:58px;top:262px;width:76px;height:22px;background:var(--brand);color:#fff;font-size:12px;font-weight:700;display:flex;align-items:center;justify-content:center}
.info{position:absolute;left:55px;top:56px;width:875px;height:31px;background:var(--info-bg);color:var(--info-ink);font-size:11px;display:flex;align-items:center;padding-left:10px}
.table{position:absolute;left:55px;top:101px;width:875px;background:#fff;border:1px solid var(--panel-line)}
.thead{height:36px;background:var(--brand);color:#fff;font-size:11px;font-weight:700;position:relative}
.row{height:35.5px;border-top:1px solid #e6e6e8;position:relative;font-size:11.5px;font-weight:500}
.cell{position:absolute;top:50%;transform:translateY(-50%)}
.thead .c1{left:26px}.thead .c2{left:207px}.thead .c3{left:413px}
.row .c1{left:28px}.row .c2{left:202px}.row .c3{left:413px}
.status{position:absolute;left:592px;top:50%;transform:translateY(-50%);width:103px;height:19px;color:#fff;font-size:11px;display:flex;align-items:center;justify-content:center}
.accepted{background:var(--accepted)}
.sent{background:var(--brand-dark)}
.pending{background:var(--pending)}
.pay{position:absolute;left:738px;top:50%;transform:translateY(-50%);width:119px;height:21px;background:var(--brand);color:#fff;font-size:12px;font-weight:700;display:flex;align-items:center;justify-content:center}
.scene{position:absolute;left:237px;top:768px;width:727px;height:123px;background:linear-gradient(180deg,rgba(76,199,242,.10) 0%,rgba(143,186,60,.18) 100%)}
.footer{position:absolute;left:0;top:891px;width:1200px;height:48px;background:var(--footer)}
.social{position:absolute;left:104px;top:20px;display:flex;gap:24px}
.social span{width:9px;height:9px;border-radius:50%;background:#8a8a8e}
.copy{position:absolute;right:126px;top:17px;font-size:11px;color:var(--ink-soft)}
</style>
</head>
<body>
<div class="top-rule"></div>
<div class="brand"><span class="brand-dot"></span>HAULVO</div>
<nav class="nav">
  <a class="active" href="#">BOOK</a>
  <a class="how" href="#">HOW IT WORKS</a>
  <a class="driver" href="#">BECOME A DRIVER</a>
  <a class="account" href="#">maren@haulvo.com</a>
</nav>

<section class="panel booking">
  <h2>BOOKING DETAILS</h2>
  <div class="label" style="left:58px;top:82px">Package Selected:</div>
  <div class="field" style="left:58px;top:109px;width:425px;height:34px">Package 1
    <svg width="8" height="12" viewBox="0 0 8 12"><path d="M4 0L8 5H0z M4 12L0 7H8z" fill="#777"/></svg>
  </div>
  <div class="label" style="left:522px;top:82px">Pick-up time selected:</div>
  <div class="field" style="left:522px;top:109px;width:425px;height:34px;padding-left:14px">July 18 at 14:13 am
    <svg width="12" height="12" viewBox="0 0 12 12"><rect x="0.5" y="1.5" width="11" height="10" fill="none" stroke="#888"/><rect x="0.5" y="1.5" width="11" height="3" fill="#888"/></svg>
  </div>
  <div class="label" style="left:58px;top:160px">Description:</div>
  <div class="field textarea" style="left:58px;top:187px;width:888px;height:68px">1 Large stove</div>
  <div class="btn-update">UPDATE</div>
</section>

<section class="panel drivers">
  <h2 style="top:26px">DRIVERS IN YOUR AREA</h2>
  <div class="info">Please stay on this page and be patient. while we contact the drivers and find you one ASAP.</div>
  <div class="table">
    <div class="thead"><span class="cell c1">Name</span><span class="cell c2">Distance (km)</span><span class="cell c3">Agreed Pick-up time</span></div>
    <div class="row" style="border-top:0"><span class="cell c1">Orin Wexley</span><span class="cell c2">4.04km away</span><span class="cell c3">July 18 at 4:13 am</span><span class="status accepted">Time Accepted</span><span class="pay">MAKE PAYMENT</span></div>
    <div class="row"><span class="cell c1">Pell Dunmore</span><span class="cell c2">5.7km away</span><span class="cell c3">-</span><span class="status sent">Request Sent</span></div>
    <div class="row"><span class="cell c1">Caspar Ilvane</span><span class="cell c2">11.13km away</span><span class="cell c3">-</span><span class="status sent">Request Sent</span></div>
    <div class="row"><span class="cell c1">Ruben Thale</span><span class="cell c2">11.91km away</span><span class="cell c3">-</span><span class="status pending">Pending</span></div>
  </div>
</section>

<div class="scene" role="img" aria-label="Flat illustration of a city skyline with recycling building, factory, forklift, rubble piles and a dump truck"></div>

<footer class="footer">
  <div class="social"><span></span><span></span><span></span><span></span></div>
  <div class="copy">Copyrights © 2017 - All Rights Reserved</div>
</footer>
</body>
</html>
```